Business Card Re- Design

We are a medical supply company.. We have three separate brands we would like to see combined to one card. I will attach all three logos. We want to have "We Love Helping People" on the card somewhere, along with website, and list of locations. The Vision and Service Values can be left off if they cannot be incorporated. Listed locations take priority over the Vision and Values

Target Market(s)

hospitals, doctors, customers

Industry/Entity Type

Medical Equipment

Contact Information for Business Card

Katrina JassoAdministrator916 17th Ave, Ste BLongmont, CO 80501Phone: 303.532.2103 Ext 1218Fax: 303.532.2897kjasso@majormedicalsupply.comwww.majormedicalsupply.comWe Love Helping People!

Requirements
Must have
• listed locations
• website
• "We Love Helping People"
• email, phone, etc
Nice to have
• Mission Vision and Values

```html
<!DOCTYPE html>
<html lang="en">
<head>
<meta charset="utf-8">
<title>Quillbrook Health Goods – Business Card</title>
<link href="https://fonts.googleapis.com/css2?family=Open+Sans:ital,wght@0,400;0,600;1,400&family=Noto+Serif:wght@700&display=swap" rel="stylesheet">
<style>
  :root {
    --page: #e9e6e1;
    --card: #ffffff;
    --card-shade: #f1f1f1;
    --blue: #2f6fc0;
    --grey: #a5a7aa;
    --ink: #1e1e1e;
    --muted: #555a60;
  }
  * { box-sizing: border-box; margin: 0; padding: 0; }
  html, body { width: 1200px; height: 892px; overflow: hidden; }
  body {
    background: var(--page);
    font-family: "Open Sans", Arial, sans-serif;
    color: var(--ink);
    position: relative;
  }
  .card {
    position: absolute;
    left: 250px;
    width: 700px;
    height: 400px;
    background: linear-gradient(180deg, var(--card) 0%, var(--card-shade) 100%);
    box-shadow: 0 6px 22px rgba(0,0,0,.18);
    overflow: hidden;
  }
  .card--front { top: 26px; }
  .card--back { top: 466px; }

  .brand {
    position: absolute;
    right: 40px;
    top: 36px;
    width: 400px;
    text-align: center;
  }
  .brand__name {
    font-size: 26px;
    font-weight: 600;
    color: var(--muted);
    white-space: nowrap;
    display: flex;
    align-items: center;
    gap: 10px;
    justify-content: center;
  }
  .brand__dot {
    width: 16px; height: 16px; border-radius: 50%;
    background: var(--blue);
    flex: none;
  }
  .brand__rule { height: 2px; background: var(--blue); margin: 6px 0; }
  .brand__line { font-size: 15px; color: var(--muted); }

  .person { position: absolute; left: 44px; top: 112px; }
  .person__name {
    font-family: "Noto Serif", Georgia, serif;
    font-weight: 700; font-size: 28px; line-height: 1.2; color: var(--blue);
  }
  .person__role { font-size: 17px; margin-top: 2px; }

  .contacts {
    position: absolute; left: 44px; top: 184px;
    list-style: none;
  }
  .contacts li {
    display: flex; align-items: center; gap: 12px;
    font-size: 16px; line-height: 1; height: 27px;
    white-space: nowrap;
  }
  .contacts svg { width: 17px; height: 17px; flex: none; }

  .wave { position: absolute; left: 0; top: 0; }
  .tagline {
    position: absolute; right: 28px; bottom: 22px;
    font-style: italic; font-size: 18px; color: #fff;
    white-space: nowrap;
  }

  .locations {
    position: absolute; left: 60px; top: 140px;
    display: flex; gap: 30px;
  }
  .locations ul {
    list-style: none;
    display: flex; flex-direction: column; gap: 12px;
  }
  .locations li {
    display: flex; align-items: center; gap: 10px;
    font-size: 20px; line-height: 1.3; white-space: nowrap;
  }
  .locations svg { width: 15px; height: 15px; flex: none; }

  .partner {
    position: absolute; left: 60px; bottom: 40px;
    font-size: 17px; font-weight: 600; color: var(--muted);
    display: flex; align-items: center; gap: 10px;
  }
  .partner__mark { width: 14px; height: 14px; background: var(--blue); }
</style>
</head>
<body>

<section class="card card--front" aria-label="Card front">
  <svg class="wave" width="700" height="400" viewBox="0 0 700 400" aria-hidden="true">
    <path d="M0 400 L0 390 C300 390 400 362 480 312 C555 268 615 252 700 250 L700 400 Z" fill="#a5a7aa"/>
    <path d="M0 400 L0 395 C300 395 400 372 480 322 C560 276 615 264 700 262 L700 400 Z" fill="#fff"/>
    <path d="M0 400 C300 400 400 380 480 332 C560 286 615 276 700 274 L700 400 Z" fill="#2f6fc0"/>
  </svg>

  <div class="brand">
    <div class="brand__name"><span class="brand__dot"></span>Quillbrook Health Goods</div>
    <div class="brand__rule"></div>
    <div class="brand__line">Home Oxygen &amp; Medical Equipment</div>
  </div>

  <div class="person">
    <h1 class="person__name">Delia Movran</h1>
    <p class="person__role">Administrator</p>
  </div>

  <ul class="contacts">
    <li><svg viewBox="0 0 18 18"><rect width="18" height="18" rx="2" fill="#2f6fc0"/><path d="M5 4l2.5 0 1 3-1.5 1a7 7 0 0 0 3 3l1-1.5 3 1V13a1 1 0 0 1-1 1A9 9 0 0 1 4 5a1 1 0 0 1 1-1z" fill="#fff"/></svg>303.648.7415 Ext 3574</li>
    <li><svg viewBox="0 0 18 18"><rect width="18" height="18" rx="2" fill="#2f6fc0"/><rect x="4" y="7" width="10" height="6" fill="#fff"/><rect x="6" y="4" width="6" height="3" fill="#fff"/></svg>303.648.7960</li>
    <li><svg viewBox="0 0 18 18"><rect width="18" height="18" rx="2" fill="#2f6fc0"/><rect x="4" y="5" width="10" height="8" fill="#fff"/><path d="M4 5l5 4 5-4" stroke="#2f6fc0" fill="none"/></svg>dmovran@quillbrookhealthgoods.com</li>
    <li><svg viewBox="0 0 18 18"><rect width="18" height="18" rx="2" fill="#2f6fc0"/><circle cx="9" cy="9" r="5" fill="none" stroke="#fff" stroke-width="1.5"/><path d="M4 9h10M9 4v10" stroke="#fff"/></svg>www.quillbrookhealthgoods.com</li>
    <li><svg viewBox="0 0 18 18"><rect width="18" height="18" rx="2" fill="#2f6fc0"/><path d="M9 15s-4-4.5-4-7.5a4 4 0 0 1 8 0C13 10.5 9 15 9 15z" fill="#fff"/><circle cx="9" cy="7.5" r="1.5" fill="#2f6fc0"/></svg>482 Ferncliff Rd, Ste C Longmont, CO 80517</li>
  </ul>

  <p class="tagline">"We Love Helping People"</p>
</section>

<section class="card card--back" aria-label="Card back">
  <div class="brand">
    <div class="brand__name"><span class="brand__dot"></span>Quillbrook Health Goods</div>
    <div class="brand__rule"></div>
    <div class="brand__line">Home Oxygen &amp; Medical Equipment</div>
  </div>

  <div class="locations">
    <ul>
      <li><svg viewBox="0 0 16 16"><path d="M8 0l2 5 5-2-3 5 3 5-5-2-2 5-2-5-5 2 3-5-3-5 5 2z" fill="#2f6fc0"/></svg>Colorado Springs</li>
      <li><svg viewBox="0 0 16 16"><path d="M8 0l2 5 5-2-3 5 3 5-5-2-2 5-2-5-5 2 3-5-3-5 5 2z" fill="#2f6fc0"/></svg>Fort Collins</li>
      <li><svg viewBox="0 0 16 16"><path d="M8 0l2 5 5-2-3 5 3 5-5-2-2 5-2-5-5 2 3-5-3-5 5 2z" fill="#2f6fc0"/></svg>Longmont</li>
    </ul>
    <ul>
      <li><svg viewBox="0 0 16 16"><path d="M8 0l2 5 5-2-3 5 3 5-5-2-2 5-2-5-5 2 3-5-3-5 5 2z" fill="#2f6fc0"/></svg>Greeley</li>
      <li><svg viewBox="0 0 16 16"><path d="M8 0l2 5 5-2-3 5 3 5-5-2-2 5-2-5-5 2 3-5-3-5 5 2z" fill="#2f6fc0"/></svg>Loveland</li>
    </ul>
    <ul>
      <li><svg viewBox="0 0 16 16"><path d="M8 0l2 5 5-2-3 5 3 5-5-2-2 5-2-5-5 2 3-5-3-5 5 2z" fill="#2f6fc0"/></svg>Denver</li>
      <li><svg viewBox="0 0 16 16"><path d="M8 0l2 5 5-2-3 5 3 5-5-2-2 5-2-5-5 2 3-5-3-5 5 2z" fill="#2f6fc0"/></svg>Lakewood</li>
      <li><svg viewBox="0 0 16 16"><path d="M8 0l2 5 5-2-3 5 3 5-5-2-2 5-2-5-5 2 3-5-3-5 5 2z" fill="#2f6fc0"/></svg>Pueblo</li>
    </ul>
  </div>

  <div class="partner"><span class="partner__mark"></span>Summitvale Care Equipment</div>
</section>

</body>
</html>
```